Stationery for Villa Marenta Design Hotel**

Who we are:

Wander on an isolated beach while breathing in the fresh, salty, sea air. Listen to the warm Pacific wind rustling through green palm trees as you walk to a pristine lagoon. Feel the delicious warmth of the sun kiss your skin; the beach is yours. At Villa Marenta you can experience a vacation in undisturbed, natural beauty. We have created a place for you to find new strength, relaxation, and inner harmony. We offer total rest to the experienced traveler from all over the world.

We are a brand new and smartly built design-hotel (under construction) close to a unique beach and a fantastic surf spot in Huatulco, Southwest Mexico.

As you can see in the attachments, we do have an established corporate design, but as for now still need a format for booklets for information around our hotel and things to do in the area, important numbers (we fill in the content for that one).

Our corporate colors:
green #64b445, brown #b07043, blue #0ab7cf, yellow # f9b02a and #fcc01a, navy #444f69
Corporate fonts:
Krub and Miller Banner.
For further information access:
www.villamarenta.example
https://slidevault.example/view/QmPxLwZrTyKsNbVcHdJe/

Social Media: VillaMarenta

Industry/Entity Type

Hotel

Font styles to use
Other font styles liked:
• Krub, Miller Banner

Requirements
Must have
• Stick to Logo Design, defined corporate elements, logo, colors, fonts and general touch and feel
Nice to have
• Who we are:

Our corporate colors:
Corporate fonts:
Krub and Miller Banner.
www.villamarenta.example

Social Media: VillaMarenta

```html
<!DOCTYPE html>
<html lang="en">
<head>
<meta charset="utf-8">
<title>Villa Marenta Design Hotel – Letterhead</title>
<link href="https://fonts.googleapis.com/css2?family=Libre+Baskerville&display=swap" rel="stylesheet">
<style>
  :root {
    --backdrop: #d9dcdd;
    --paper: #ffffff;
    --teal: #0ab7cf;
    --teal-deep: #0a7f8f;
    --green: #8cc63f;
    --gold: #c9961c;
    --ink-teal: #157f8c;
    --ink-grey: #6b6f73;
    --rule: #9a9ea2;
  }
  * { box-sizing: border-box; margin: 0; padding: 0; }
  html, body {
    width: 1200px; height: 784px; overflow: hidden;
    background: var(--backdrop);
    font-family: "Libre Baskerville", Georgia, serif;
  }
  .letterhead {
    position: absolute; left: 340px; top: 22px;
    width: 520px; height: 740px;
    background: var(--paper);
    box-shadow: 0 6px 18px rgba(0,0,0,.12);
    overflow: hidden;
  }
  .brand {
    position: absolute; left: 44px; top: 40px;
    display: flex; align-items: center; gap: 10px;
    color: var(--gold); font-size: 17px; letter-spacing: .04em;
  }
  .brand-mark { width: 14px; height: 14px; border: 2px solid var(--gold); }
  .corner { position: absolute; width: 190px; height: 80px; }
  .corner--bottom-left { left: 0; bottom: 0; }
  .corner--top-right { right: 0; top: 0; transform: rotate(180deg); }
  .footer {
    position: absolute; left: 0; right: 0; bottom: 42px;
    text-align: center;
  }
  .footer-icons {
    display: flex; justify-content: center; align-items: center; gap: 8px;
    margin-bottom: 8px;
  }
  .footer-rule { width: 70px; height: 1px; background: var(--rule); margin: 0 6px; }
  .footer-icon { width: 14px; height: 14px; }
  .footer-address { color: var(--ink-teal); font-size: 10px; margin-bottom: 5px; }
  .footer-contact { color: var(--ink-grey); font-size: 8.5px; }
</style>
</head>
<body>
<main class="letterhead">
  <div class="brand"><span class="brand-mark"></span>Villa Marenta</div>

  <svg class="corner corner--bottom-left" viewBox="0 0 190 80" aria-hidden="true">
    <defs>
      <linearGradient id="bandFade" x1="0" y1="0" x2="1" y2="0">
        <stop offset="0" stop-color="var(--teal-deep)"/>
        <stop offset="1" stop-color="var(--teal)"/>
      </linearGradient>
    </defs>
    <polygon points="0,26 0,80 160,80" fill="url(#bandFade)"/>
    <polyline points="0,18 8,18 172,80" fill="none" stroke="var(--green)" stroke-width="2"/>
    <polyline points="0,11 14,11 184,80" fill="none" stroke="var(--gold)" stroke-width="2"/>
  </svg>

  <svg class="corner corner--top-right" viewBox="0 0 190 80" aria-hidden="true">
    <defs>
      <linearGradient id="bandFadeTop" x1="0" y1="0" x2="1" y2="0">
        <stop offset="0" stop-color="var(--teal-deep)"/>
        <stop offset="1" stop-color="var(--teal)"/>
      </linearGradient>
    </defs>
    <polygon points="0,26 0,80 160,80" fill="url(#bandFadeTop)"/>
    <polyline points="0,18 8,18 172,80" fill="none" stroke="var(--green)" stroke-width="2"/>
    <polyline points="0,11 14,11 184,80" fill="none" stroke="var(--gold)" stroke-width="2"/>
  </svg>

  <footer class="footer">
    <div class="footer-icons">
      <span class="footer-rule"></span>
      <svg class="footer-icon" viewBox="0 0 14 14" aria-label="Location"><circle cx="7" cy="7" r="7" fill="var(--gold)"/><path d="M7 3.2a2.3 2.3 0 0 0-2.3 2.3C4.7 7.3 7 10.6 7 10.6s2.3-3.3 2.3-5.1A2.3 2.3 0 0 0 7 3.2z" fill="#fff"/><circle cx="7" cy="5.5" r=".9" fill="var(--gold)"/></svg>
      <svg class="footer-icon" viewBox="0 0 14 14" aria-label="Phone"><circle cx="7" cy="7" r="7" fill="var(--gold)"/><path d="M5 3.5l1.2 1.8-.8.9c.5 1 1.3 1.8 2.3 2.3l.9-.8 1.8 1.2-.7 1.3C7.2 10.4 3.6 6.8 3.8 4.2z" fill="#fff"/></svg>
      <svg class="footer-icon" viewBox="0 0 14 14" aria-label="Mobile"><circle cx="7" cy="7" r="7" fill="var(--gold)"/><rect x="5" y="3.3" width="4" height="7.4" rx=".8" fill="#fff"/></svg>
      <svg class="footer-icon" viewBox="0 0 14 14" aria-label="Email"><circle cx="7" cy="7" r="7" fill="var(--gold)"/><rect x="3.6" y="4.6" width="6.8" height="4.8" fill="#fff"/><path d="M3.6 4.6L7 7.4l3.4-2.8" fill="none" stroke="var(--gold)" stroke-width=".8"/></svg>
      <svg class="footer-icon" viewBox="0 0 14 14" aria-label="Website"><circle cx="7" cy="7" r="7" fill="var(--gold)"/><circle cx="7" cy="7" r="3.6" fill="none" stroke="#fff" stroke-width=".9"/><path d="M3.4 7h7.2M7 3.4v7.2" stroke="#fff" stroke-width=".9"/></svg>
      <span class="footer-rule"></span>
    </div>
    <p class="footer-address">Villa Marenta, Playa Serena, Bahía Lumbre, Mexiko</p>
    <p class="footer-contact">+52 1 (555) 014 3920 | hello@villamarenta.example | www.villamarenta.example</p>
  </footer>
</main>
</body>
</html>
```